Optical shop needs a signage that attracts families such as parents and kids

My shop name is Mivo optical. I need a signage for my optical shop that can attract families, targeting mainly kids and their adults. My shop is situated in neighborhood areas and sells affordable spectacles. The interior of my shop is clean and white base, very comfortable feeling that makes people feel like they have come home. Signage should not be too fancy and colourful. I have attached a mascot for my signage too, it is a cat that wear spectacles. You can either use or don't use the mascot for the design. Let me view your creative side. :)

The theme would be more of Japanese. Please do something that has Japanese style or elements for the signage logo design. Colours used can be more of Japanese origin.
Updates

Reason: There are not enough designs to choose from. Please help to send in more designs. Thanks.

The theme would be more Japanese style as people would like to associate my shop name with it.

Target Market(s)

Families, teens and elderly

Industry/Entity Type

Shop

Font styles to use
Script

```html
<!DOCTYPE html>
<html lang="en">
<head>
<meta charset="utf-8">
<title>Mivo Optical — Shop Signage</title>
<link rel="stylesheet" href="https://fonts.googleapis.com/css2?family=Playball&display=swap">
<style>
  :root {
    --sign-red-left: #f0577a;
    --sign-red-mid: #ee4767;
    --sign-red-right: #ec3a48;
    --ornament-tint: rgba(255, 210, 220, 0.22);
    --mascot-white: #fbf7f6;
    --mascot-shade: #e9e1df;
    --name-fill-top: #ffffff;
    --name-fill-bottom: #f6c9d6;
    --name-edge: #d8253d;
    --name-shadow: rgba(120, 10, 30, 0.45);
  }
  html, body {
    margin: 0;
    padding: 0;
    width: 1200px;
    height: 309px;
    overflow: hidden;
    background: #ffffff;
  }
  .signboard {
    position: relative;
    width: 1200px;
    height: 309px;
    overflow: hidden;
    background: linear-gradient(90deg, var(--sign-red-left) 0%, var(--sign-red-mid) 50%, var(--sign-red-right) 100%);
  }
  .ornament {
    position: absolute;
    top: 0;
    height: 309px;
  }
  .ornament--left {
    left: 0;
    width: 330px;
    background: radial-gradient(ellipse at 50% 50%, var(--ornament-tint) 0%, rgba(255,210,220,0) 70%);
  }
  .ornament--right {
    right: 0;
    width: 360px;
    background: radial-gradient(ellipse at 55% 50%, var(--ornament-tint) 0%, rgba(255,210,220,0) 70%);
  }
  .mascot {
    position: absolute;
    left: 40px;
    top: 40px;
    width: 222px;
    height: 232px;
  }
  .shop-name {
    position: absolute;
    left: 262px;
    top: 70px;
    margin: 0;
    padding: 10px 50px 20px 40px;
    font-family: "Playball", cursive;
    font-weight: 400;
    font-size: 170px;
    line-height: 1;
    letter-spacing: 1px;
    white-space: nowrap;
    color: var(--name-fill-top);
    background: linear-gradient(180deg, var(--name-fill-top) 40%, var(--name-fill-bottom) 90%);
    -webkit-background-clip: text;
    background-clip: text;
    -webkit-text-fill-color: transparent;
    -webkit-text-stroke: 2px var(--name-edge);
    paint-order: stroke fill;
    filter: drop-shadow(3px 5px 4px var(--name-shadow));
  }
</style>
</head>
<body>
  <div class="signboard">
    <div class="ornament ornament--left" role="img" aria-label="Faint floral scroll pattern"></div>
    <div class="ornament ornament--right" role="img" aria-label="Faint floral scroll pattern"></div>

    <svg class="mascot" viewBox="0 0 222 232" role="img" aria-label="Shop mascot: white beckoning cat wearing round spectacles">
      <defs>
        <linearGradient id="mascot-tone" x1="0" y1="0" x2="0" y2="1">
          <stop offset="0" stop-color="var(--mascot-white)"/>
          <stop offset="1" stop-color="var(--mascot-shade)"/>
        </linearGradient>
      </defs>
      <rect x="0" y="0" width="222" height="232" rx="60" fill="url(#mascot-tone)"/>
    </svg>

    <h1 class="shop-name">Mivo Optical</h1>
  </div>
</body>
</html>
```